DJ Colm Vetter

I'm looking for a professional but still artsy/progressive design. I come from a hip hop/club DJ background playing a lot of underground music but have switched to doing more corporate parties and weddings recently. I am all about keeping the dancefloor moving and emotionally connecting with the crowd. I'd like a trendy/updated color palette. Something that's clean enough that looks professional but also trendy enough to convey that by the end of the night we'll be sweatily dancing to the latest hits. Some designers/artists I like: Tarn Olquist, Pavel Remy, Wendell Quarrie, Lumeno 7400, Silas Dravin.

```html
<!DOCTYPE html>
<html lang="en">
<head>
<meta charset="utf-8">
<title>DJ Colm Vetter – Business Card</title>
<link rel="stylesheet" href="https://fonts.googleapis.com/css2?family=Bebas+Neue&family=Open+Sans:wght@400;600&display=swap">
<style>
  :root {
    --page-bg: #141414;
    --card-bg: #1f1f21;
    --card-edge: #2a2a2c;
    --text-white: #f2f2f2;
    --text-soft: #cfcfcf;
    --silver: #bdbdbd;
    --accent-blue: #5ab8ea;
    --divider: #3a3a3c;
  }
  * { margin: 0; padding: 0; box-sizing: border-box; }
  html, body {
    width: 1200px; height: 900px; overflow: hidden;
    background: var(--page-bg);
  }
  .canvas { position: relative; width: 1200px; height: 900px; }

  .card {
    position: absolute;
    width: 525px; height: 300px;
    border-radius: 18px;
    background: linear-gradient(160deg, #262628 0%, var(--card-bg) 55%, #1a1a1b 100%);
    border: 1px solid var(--card-edge);
    box-shadow: 0 10px 30px rgba(0,0,0,0.55);
    overflow: hidden;
  }
  .card-front { left: 110px; top: 110px; }
  .card-back  { left: 565px; top: 480px; }

  /* front */
  .front-name {
    position: absolute; left: 0; right: 0; top: 105px;
    text-align: center;
    font-family: "Bebas Neue", sans-serif;
    font-size: 62px; letter-spacing: 1px;
    color: var(--silver);
  }
  .front-web {
    position: absolute; right: 40px; bottom: 32px;
    font-family: "Open Sans", sans-serif;
    font-size: 13px; color: var(--text-soft);
  }

  /* back */
  .brand {
    position: absolute; right: 36px; top: 40px;
    display: flex; align-items: center; gap: 12px;
  }
  .brand-dot {
    width: 22px; height: 22px; border-radius: 50%;
    background: var(--accent-blue);
  }
  .brand-name {
    font-family: "Bebas Neue", sans-serif;
    font-size: 58px; line-height: 1;
    color: var(--text-white);
  }
  .divider {
    position: absolute; left: 36px; right: 36px; top: 132px;
    height: 1px; background: var(--divider);
  }
  .address {
    position: absolute; right: 36px; top: 146px;
    text-align: right;
    font-family: "Open Sans", sans-serif;
    font-size: 14px; line-height: 1.35; color: var(--text-white);
  }
  .person { position: absolute; left: 36px; top: 180px; }
  .person-name {
    font-family: "Bebas Neue", sans-serif;
    font-size: 26px; line-height: 1; color: var(--accent-blue);
  }
  .person-role {
    font-family: "Open Sans", sans-serif;
    font-size: 14px; color: var(--text-white);
  }
  .contacts {
    list-style: none; margin-top: 10px;
    font-family: "Open Sans", sans-serif;
    font-size: 14px; line-height: 1.3; color: var(--text-white);
  }
  .contacts li { display: flex; align-items: center; gap: 8px; }
  .contacts svg { width: 12px; height: 12px; fill: var(--accent-blue); flex: none; }
</style>
</head>
<body>
<main class="canvas">

  <section class="card card-front" aria-label="Card front">
    <div class="front-name">DJ Colm Vetter</div>
    <div class="front-web">www.colmvetter.com</div>
  </section>

  <section class="card card-back" aria-label="Card back">
    <div class="brand">
      <span class="brand-dot"></span>
      <span class="brand-name">DJ Colm Vetter</span>
    </div>
    <div class="divider"></div>
    <address class="address" style="font-style:normal">
      48, Harlow Lane Studios<br>
      Westmere, 604117
    </address>
    <div class="person">
      <div class="person-name">Jonah Whitcombe</div>
      <div class="person-role">Managing Director</div>
      <ul class="contacts">
        <li>
          <svg viewBox="0 0 12 12" aria-hidden="true"><path d="M2.5 1 4.5 1 5.3 3.4 4 4.4C4.7 5.9 6 7.2 7.6 8L8.6 6.7 11 7.5 11 9.5C11 10.3 10.3 11 9.5 11 5 11 1 7 1 2.5 1 1.7 1.7 1 2.5 1Z"/></svg>
          044-310 552 918
        </li>
        <li>
          <svg viewBox="0 0 12 12" aria-hidden="true"><path d="M3.5 0.5H8.5A1 1 0 0 1 9.5 1.5V10.5A1 1 0 0 1 8.5 11.5H3.5A1 1 0 0 1 2.5 10.5V1.5A1 1 0 0 1 3.5 0.5ZM3.7 1.8V9H8.3V1.8ZM6 9.6A0.7 0.7 0 1 0 6 11 0.7 0.7 0 1 0 6 9.6Z"/></svg>
          044-310 552 927
        </li>
        <li>
          <svg viewBox="0 0 12 12" aria-hidden="true"><path d="M1 2.5H11V9.5H1ZM1.8 3.2 6 6.4 10.2 3.2V3.1H1.8Z"/></svg>
          info@colmvetter.com
        </li>
      </ul>
    </div>
  </section>

</main>
</body>
</html>
```